Email mail merge - not a marketing email, this is an update email sent regularly to our members

HI I need a generic email designed to send out to our members, this is a tri-weekly (monday - updates - Wednesday - updates and Fridays - weekly round up.

we would like it to have within the mail body, 3 interactive, changeable boxes for example "quote of the week', 'top performer' and something else, It would be great if we can remove a box if and when we choose.
Our company is called Kr4ve Amusements or Kr4ve for short.
It needs to be in HTML to fit with our back office software.
We have all the logos for you already which I have included, I have also included our current email header.
our websites are...
kr4vamu.cub - This is our members back end site.
kr4vamu.com - This is our gaming site.
Please email me on derek@kr4vamu.com if you have any queries

Target Market(s)

All of our members - We currently have over 400 but it is growing at an astronomical rate.

Industry/Entity Type

Marketing

Font styles to use
Serif
Decorative
Script

Requirements
Must have
• At least two interactive, changeable boxes/areas that I can put photo's or quotes in to. I would also like some guidelines as to how I change these myself.
• The colours should be inline with our kr4vamu.club site.
Nice to have
• This is a positive email update so it needs to look clean and clear but vibrant, we are a unique company that is breaking records and is very successful.
• Our members have the ability and some already are earning vast sums of money.

```html
<!DOCTYPE html>
<html lang="en">
<head>
<meta charset="utf-8">
<title>Kr4ve Amusements – Member Update</title>
<link rel="stylesheet" href="https://fonts.googleapis.com/css2?family=Jost:wght@400;500;600&family=Libre+Baskerville&family=Arimo:ital,wght@0,400;0,700;1,700&display=swap">
<style>
:root{
  --frame:#9aa3a3;
  --paper:#ffffff;
  --mist:#f3f3f4;
  --ink:#1b2a2c;
  --body:#4a4f50;
  --muted:#9a9fa0;
  --brand-grey:#8e9494;
  --teal-deep:#1d4a4a;
  --teal-dark:#123536;
  --night:#0d2426;
  --aqua:#7fe3d7;
  --gold:#f5a800;
  --rule:#c9cccc;
}
*{box-sizing:border-box;margin:0;padding:0}
html,body{width:1200px;height:4119px;overflow:hidden}
body{background:var(--frame);position:relative;font-family:"Arimo",Arial,sans-serif;color:var(--body)}
.preheader{position:absolute;top:34px;left:0;width:1200px;text-align:center;color:#fff;font-size:22px}
.mail{position:absolute;left:47px;top:96px;width:1106px;height:3941px;background:var(--paper)}
.abs{position:absolute}

.brand{left:0;width:1106px;top:90px;text-align:center;font-family:"Jost",sans-serif;font-weight:500;font-size:84px;color:var(--brand-grey);line-height:1}
.devices{left:90px;top:275px;width:893px;height:549px;border-radius:18px;background:linear-gradient(160deg,#e6e9ea 0%,#3b4446 35%,#1f3a5a 60%,#d8dcdd 100%)}

.quote-band{left:0;top:1016px;width:1106px;height:302px;background:var(--mist)}
.ribbon{left:0;top:914px}
.ribbon-title{left:0;top:944px;width:1106px;text-align:center;color:#fff;font-family:"Jost",sans-serif;font-weight:500;font-size:52px;letter-spacing:1px;line-height:60px}
.quote-text{left:0;top:1115px;width:1106px;text-align:center;font-family:"Libre Baskerville",serif;font-size:35px;line-height:46px;color:var(--ink)}
.quote-rule{left:465px;top:1250px;width:176px;height:5px;background:var(--teal-deep)}

.performer{left:0;top:1318px;width:1106px;height:540px;background:var(--night)}
.portrait{left:57px;top:61px;width:412px;height:414px;border:12px solid #5d6a6c;background:radial-gradient(circle at 50% 40%,#f4e2c4 0%,#d9c9a4 40%,#eef0f1 75%)}
.performer-title{left:524px;top:58px;font-family:"Jost",sans-serif;font-weight:600;font-size:64px;letter-spacing:1px;color:var(--aqua);line-height:60px}
.performer-sub{left:526px;top:128px;font-family:"Jost",sans-serif;font-weight:600;font-size:38px;color:#fff;line-height:40px}
.performer-name{left:533px;top:196px;font-style:italic;font-weight:700;font-size:30px;color:var(--gold);line-height:36px}
.performer-copy{left:533px;top:262px;width:510px;font-size:25px;line-height:37px;color:#fff}

.heading{left:0;width:1106px;text-align:center;font-family:"Jost",sans-serif;font-weight:600;font-size:64px;color:var(--ink);line-height:62px}
.subheading{left:0;width:1106px;text-align:center;font-family:"Jost",sans-serif;font-weight:500;font-size:32px;letter-spacing:1px;color:#3a4345;line-height:32px}
.copy{left:72px;width:962px;text-align:center;font-size:25px;line-height:38px;color:var(--body)}
.divider{left:310px;top:2583px;width:486px;height:2px;background:#e4e6e6}

.dash{left:49px;width:1008px;border-top:3px dashed var(--rule)}
.office-head{left:49px;top:3459px;font-family:"Jost",sans-serif;font-weight:500;font-size:30px;letter-spacing:2px;color:var(--muted);line-height:30px}
.office-text{left:49px;top:3526px;font-size:25px;line-height:37.6px;color:var(--muted)}
.office-text strong{font-weight:400;color:var(--ink)}
.brand-small{left:574px;top:3520px;width:486px;text-align:center;font-family:"Jost",sans-serif;font-weight:500;font-size:48px;color:var(--brand-grey);line-height:56px}
.cta{left:574px;top:3617px;width:486px;height:66px;border-radius:33px;background:var(--gold);color:var(--ink);font-family:"Jost",sans-serif;font-weight:500;font-size:25px;letter-spacing:1px;display:flex;align-items:center;padding-left:56px;text-decoration:none}
.cta-sep{position:absolute;left:396px;top:14px;width:2px;height:38px;background:var(--ink)}
.cta svg{position:absolute;left:422px;top:14px}
.social{left:0;top:3836px;width:1106px;display:flex;justify-content:center;gap:40px}
.social span{width:28px;height:28px;border-radius:50%;background:#a8adae}
</style>
</head>
<body>
<div class="preheader">Not viewing properly? View this mail in web browser</div>

<main class="mail">
  <div class="abs brand">Kr4ve Amusements</div>
  <div class="abs devices" role="img" aria-label="Laptop, tablet and phone showing the Kr4ve gaming and club websites"></div>

  <div class="abs quote-band"></div>
  <svg class="abs ribbon" width="1106" height="140" viewBox="0 0 1106 140" aria-hidden="true">
    <polygon points="150,45 230,45 230,128 150,128 178,86" fill="var(--teal-deep)"/>
    <polygon points="956,45 876,45 876,128 956,128 928,86" fill="var(--teal-deep)"/>
    <polygon points="214,106 230,128 230,106" fill="var(--teal-dark)"/>
    <polygon points="892,106 876,128 876,106" fill="var(--teal-dark)"/>
    <rect x="214" y="11" width="678" height="95" fill="var(--teal-deep)"/>
  </svg>
  <div class="abs ribbon-title">QUOTE OF THE WEEK</div>
  <p class="abs quote-text">Lorem isum dolosr sit amet esta di maria<br>nuno valencia ed di mordor.</p>
  <div class="abs quote-rule"></div>

  <section class="abs performer">
    <div class="abs portrait" role="img" aria-label="Portrait photo of this week's top performer"></div>
    <div class="abs performer-title">TOP PERFORMER</div>
    <div class="abs performer-sub">OF THE WEEK</div>
    <div class="abs performer-name">Marisol Quenby</div>
    <p class="abs performer-copy">Nulla vestibulum mauris ac est consequat, quis dapibus diam porta. Suspendisse non ligula lacinia nisi interdum vulputate in sed purus. Quisque eget felis non libero euismod ultricies tristique at nibh.</p>
  </section>

  <h2 class="abs heading" style="top:1913px">LATEST NEWS</h2>
  <h3 class="abs subheading" style="top:2011px">THIS WEEK’S NEWS</h3>
  <p class="abs copy" style="top:2112px">Join the KR4VE CLUB Membership and Rewards Program today to start earning income with a new dedicated Gaming and Sport Betting Service directed to the networking industry.</p>
  <p class="abs copy" style="top:2263px">KR4VE CLUB caters to all levels of users with its range of six rewarding membership plans:, Bronze, Silver, Gold, Ruby, Emerald and Diamond Founder, The Diamond Founder plan is much sought after because there are barely one hundred such memberships on offer worldwide. Nonetheless, each of these plans is a package of delights: earn commissions, share your moneymaking adventure at KR4VE CLUB throughout the membership lifetime, and carry no liability of negative monthly spillovers. It's like you sign a fun contract once you choose us!</p>

  <div class="abs divider"></div>

  <h2 class="abs heading" style="top:2652px">WEEKLY UPDATES</h2>
  <h3 class="abs subheading" style="top:2747px">CHECK LATEST UPDATES</h3>
  <p class="abs copy" style="top:2851px">Join the KR4VE CLUB Membership and Rewards Program today to start earning income with a new dedicated Gaming and Sport Betting Service directed to the networking industry.</p>
  <p class="abs copy" style="top:3002px">KR4VE CLUB caters to all levels of users with its range of six rewarding membership plans:, Bronze, Silver, Gold, Ruby, Emerald and Diamond Founder, The Diamond Founder plan is much sought after because there are barely one hundred such memberships on offer worldwide. Nonetheless, each of these plans is a package of delights: earn commissions, share your moneymaking adventure at KR4VE CLUB throughout the membership lifetime, and carry no liability of negative monthly spillovers. It's like you sign a fun contract once you choose us!</p>

  <div class="abs dash" style="top:3397px"></div>

  <footer>
    <div class="abs office-head">REGISTERED OFFICES</div>
    <p class="abs office-text">Suite 4, Harbour Court Linden Quay,<br>Gibraltar, British Overseas Territory<br>on the south coast of Spain<br>Ph:<strong>1300 555 218</strong><br>Email: <strong>support@kr4vamu.com</strong></p>
    <div class="abs brand-small">Kr4ve Amusements</div>
    <a class="abs cta">VISIT OUR CLUB WEBSITE<span class="cta-sep"></span>
      <svg width="38" height="38" viewBox="0 0 38 38" aria-hidden="true"><circle cx="19" cy="19" r="16" fill="none" stroke="var(--ink)" stroke-width="3"/><path d="M11 19h14M19 12l7 7-7 7" fill="none" stroke="var(--ink)" stroke-width="3"/></svg>
    </a>
    <div class="abs dash" style="top:3781px"></div>
    <div class="abs social" aria-label="Social links"><span></span><span></span><span></span><span></span><span></span></div>
  </footer>
</main>
</body>
</html>
```